Business Card Design Project

- makeup artist business card

- original and creative

- Elegant design

- Feel free to come out with cool designs but stick to being elegant and attractive

- Design relates to makeup

- includes name, occupation, contact numbers, email, website

- regular size business card

- round corner card

- double sided

- on 1 side it should just have the website name in the center " moonveilstudio.net "

Industry/Entity Type

Business

Requirements
Must have
• Delia Marsh
Makeup Artist
USA: +1 (415)772-0461
Singapore: +65 82307915
deliamarsh@moonveilstudio.net
www.moonveilstudio.net
Should not have
• nothing cartoon looking.
Pictures of makeup being grab from the internet.. Examples: eyes or lips.

```html
<!DOCTYPE html>
<html lang="en">
<head>
<meta charset="utf-8">
<title>Delia Marsh — Makeup Artist Business Card</title>
<link rel="stylesheet" href="https://fonts.googleapis.com/css2?family=Parisienne&family=La+Belle+Aurore&family=Didact+Gothic&display=swap">
<style>
  :root {
    --page-bg: #ecebea;
    --card-black: #161515;
    --card-paper: #f6f4f1;
    --ink: #141212;
    --silver: #f2f2f2;
    --wash-rose: rgba(212, 88, 126, 0.78);
    --wash-pink: rgba(232, 140, 150, 0.62);
    --wash-peach: rgba(242, 195, 143, 0.5);
    --wash-clear: rgba(246, 244, 241, 0);
  }
  * { box-sizing: border-box; margin: 0; padding: 0; }
  html, body {
    width: 1200px;
    height: 1200px;
    overflow: hidden;
    background: var(--page-bg);
  }
  .canvas {
    position: relative;
    width: 1200px;
    height: 1200px;
  }
  .card {
    position: absolute;
    left: 150px;
    width: 900px;
    height: 514px;
    border-radius: 28px;
    overflow: hidden;
    box-shadow: 0 10px 30px rgba(0,0,0,0.12);
  }
  /* Back side */
  .card--back {
    top: 44px;
    background: var(--card-black);
    display: flex;
    align-items: center;
    justify-content: center;
  }
  .back-website {
    font-family: "La Belle Aurore", cursive;
    font-size: 66px;
    color: var(--silver);
    letter-spacing: 1px;
  }
  /* Front side */
  .card--front {
    top: 642px;
    background: var(--card-paper);
  }
  .makeup-wash {
    position: absolute;
    inset: 0;
    background: linear-gradient(100deg,
      var(--wash-rose) 0%,
      var(--wash-pink) 28%,
      var(--wash-peach) 50%,
      var(--wash-clear) 74%);
  }
  .identity {
    position: absolute;
    right: 70px;
    top: 150px;
    text-align: right;
  }
  .name {
    font-family: "Parisienne", cursive;
    font-weight: 400;
    font-size: 84px;
    line-height: 1;
    color: var(--ink);
    white-space: nowrap;
  }
  .occupation {
    font-family: "Didact Gothic", sans-serif;
    font-size: 23px;
    letter-spacing: 1.5px;
    color: var(--ink);
    margin-top: -2px;
    padding-right: 22px;
  }
  .contacts {
    position: absolute;
    right: 50px;
    bottom: 30px;
    list-style: none;
    text-align: right;
    font-family: "Didact Gothic", sans-serif;
    font-size: 26px;
    line-height: 1.3;
    color: var(--ink);
  }
</style>
</head>
<body>
  <main class="canvas">
    <section class="card card--back" aria-label="Card back">
      <p class="back-website">moonveilstudio.net</p>
    </section>

    <section class="card card--front" aria-label="Card front">
      <div class="makeup-wash" role="img" aria-label="Watercolour painting of glossy pink lips on a soft peach wash"></div>
      <div class="identity">
        <h1 class="name">Delia Marsh</h1>
        <p class="occupation">MAKEUP ARTIST</p>
      </div>
      <ul class="contacts">
        <li>USA: +1 (415)772-0461</li>
        <li>Singapore: +65 82307915</li>
        <li>deliamarsh@moonveilstudio.net</li>
        <li>www.moonveilstudio.net</li>
      </ul>
    </section>
  </main>
</body>
</html>
```